Norrell Advisory WA Business Card

Create an interesting, eye catching and colourful two sided business card. We are a business consulting operation assisting SME's improve all areas of their business. We provide consulting services to assist SME's to create a culture of continuous improvement, making a positive difference in the business. Our tag line is Small changes, big rewards. We want to create a well recognised, innovative brand that can be continued throughout our website, social media and email correspondence.

Target Market(s)

Small to Medium Enterprise Business Owners

Industry/Entity Type

Business Consultant

Contact Information for Business Card

Name of Business: Norrell Advisory - Steady Steps Greater Gains
Derek Holloway Ph 0407385510 Megan Holloway Ph 0407913847
Email norrelladvisorywa@mailbox-example.com
Web address TBA
FaceBook page TBA

BACKSIDE OF CARD

Providing assistance with:

• Organisation & Efficiency
• Revenue generation & Marketing
• Financial Management
• Production quality & delivery
• Systems & Process documentation
• Exit Strategy

Font styles to use
Other font styles liked:
• Calibri

Colors

Designer to choose colors to be used in the design.

Requirements
Must have
• Calibri font

```html
<!DOCTYPE html>
<html lang="en">
<head>
<meta charset="utf-8">
<title>Norrell Advisory WA Business Card</title>
<link rel="stylesheet" href="https://fonts.googleapis.com/css2?family=Open+Sans:ital,wght@0,400;0,600;0,700;1,700&display=swap">
<style>
  :root {
    --page: #e7e7e7;
    --card-light: #ffffff;
    --card-dark-top: #2b2b2b;
    --card-dark-bottom: #1b1b1b;
    --ink: #333333;
    --ink-soft: #666666;
    --ink-muted: #555555;
    --rule: #8a8a8a;
    --blue: #1f8ec8;
    --blue-light: #3aa3d6;
    --light-text: #e6e6e6;
  }
  * { box-sizing: border-box; margin: 0; padding: 0; }
  html, body {
    width: 1125px; height: 1200px; overflow: hidden;
    background: var(--page);
    font-family: "Open Sans", Calibri, Arial, sans-serif;
  }
  .card {
    position: absolute; left: 171px; width: 826px; height: 472px;
    border-radius: 24px; overflow: hidden;
  }
  .card--front { top: 106px; background: var(--card-light); }
  .card--back {
    top: 639px;
    background: linear-gradient(160deg, var(--card-dark-top), var(--card-dark-bottom));
  }

  /* front */
  .brand { position: absolute; left: 40px; width: 355px; text-align: center; }
  .brand__mark {
    width: 96px; height: 96px; margin: 0 auto 42px;
    background: var(--blue);
  }
  .brand--front { top: 126px; }
  .brand__name {
    font-weight: 700; font-size: 30px; letter-spacing: 0.2px;
    color: var(--ink); line-height: 1; white-space: nowrap;
  }
  .brand__tagline {
    margin-top: 6px; font-weight: 600; font-size: 12.5px;
    letter-spacing: 4.1px; color: var(--ink-muted); white-space: nowrap;
  }
  .divider {
    position: absolute; left: 414px; top: 103px;
    width: 1px; height: 224px; background: var(--rule);
  }
  .contacts { position: absolute; left: 451px; top: 98px; }
  .person__name {
    font-weight: 700; font-size: 34px; line-height: 1.05;
    color: var(--ink-soft); white-space: nowrap;
  }
  .person__phone {
    font-weight: 700; font-size: 25px; line-height: 1;
    color: var(--ink-soft); margin-left: 2px;
  }
  .person + .person { margin-top: 16px; }
  .links { list-style: none; margin-top: 22px; margin-left: 3px; }
  .links li {
    display: flex; align-items: center; gap: 9px;
    font-size: 17px; line-height: 25px; color: var(--ink-soft);
  }
  .links svg { width: 16px; height: 16px; flex: none; }
  .base-band {
    position: absolute; left: 0; bottom: 0; width: 826px; height: 56px;
    background: linear-gradient(90deg, var(--blue), var(--blue-light));
  }

  /* back */
  .brand--back { top: 160px; left: 90px; width: 260px; }
  .brand--back .brand__mark { width: 90px; height: 90px; margin-bottom: 22px; }
  .brand--back .brand__name { font-size: 22px; color: var(--light-text); }
  .services { position: absolute; left: 350px; top: 140px; color: var(--light-text); }
  .services__title { font-weight: 700; font-style: italic; font-size: 24px; line-height: 1.3; }
  .services__list { list-style: none; margin-top: 6px; }
  .services__list li {
    font-size: 17.5px; line-height: 25px; padding-left: 20px; position: relative;
  }
  .services__list li::before {
    content: ""; position: absolute; left: 4px; top: 11px;
    width: 5px; height: 5px; border-radius: 50%; background: var(--light-text);
  }
</style>
</head>
<body>

<section class="card card--front" aria-label="Card front">
  <div class="brand brand--front">
    <div class="brand__mark"></div>
    <div class="brand__name">NORRELL ADVISORY</div>
    <div class="brand__tagline">STEADY STEPS GREATER GAINS</div>
  </div>

  <div class="divider"></div>

  <div class="contacts">
    <div class="person">
      <div class="person__name">DEREK HOLLOWAY</div>
      <div class="person__phone">0407385510</div>
    </div>
    <div class="person">
      <div class="person__name">MEGAN HOLLOWAY</div>
      <div class="person__phone">0407913847</div>
    </div>
    <ul class="links">
      <li><svg viewBox="0 0 16 16" aria-hidden="true"><rect x="1" y="1" width="14" height="14" fill="#666"/></svg>norrelladvisorywa</li>
      <li><svg viewBox="0 0 16 16" aria-hidden="true"><rect x="1" y="3.5" width="14" height="9.5" fill="none" stroke="#666" stroke-width="1.6"/><path d="M1.5 4 8 9l6.5-5" fill="none" stroke="#666" stroke-width="1.6"/></svg>norrelladvisorywa@mailbox-example.com</li>
      <li><svg viewBox="0 0 16 16" aria-hidden="true"><circle cx="8" cy="8" r="7" fill="#666"/><path d="M1 8h14M8 1c-3 3.5-3 10.5 0 14M8 1c3 3.5 3 10.5 0 14" fill="none" stroke="#fff" stroke-width="1"/></svg>www.norrelladvisorywa-example.com</li>
    </ul>
  </div>

  <div class="base-band" role="img" aria-label="Decorative multicoloured wave band along the card's lower edge"></div>
</section>

<section class="card card--back" aria-label="Card back">
  <div class="brand brand--back">
    <div class="brand__mark"></div>
    <div class="brand__name">NORRELL ADVISORY</div>
  </div>
  <div class="services">
    <h2 class="services__title">Providing assistance with</h2>
    <ul class="services__list">
      <li>Organisation &amp; Efficiency</li>
      <li>Revenue generation &amp; Marketing</li>
      <li>Financial Management</li>
      <li>Production quality &amp; delivery</li>
      <li>Systems &amp; Process documentation</li>
      <li>Exit Strategy</li>
    </ul>
  </div>
</section>

</body>
</html>
```